Breakfast Cafe - The Sunny Nook

It is for my breakfast and lunch cafe with a hawaiian / beach theme. I am open 7 days a week from 7am to 2pm. We serve traditional American food such as omelettes, pancakes, burgers and sandwiches. I'll upload my old card and my new logo to be used. We have a lot of day to day regulars who eat there during the week, our t-shirts actually say 'Locals Only' on them. Hope this helps. Thanks.

Target Market(s)

anyone who has an appetite!

Industry/Entity Type

American Restaurant

Contact Information for Business Card

4815C Marlow Grove Avenue
Long Beach, California
(555) 731-2294

Requirements
Must have
• Address and phone number easily readable.
Nice to have
• beach or tropical theme

```html
<!DOCTYPE html>
<html lang="en">
<head>
<meta charset="utf-8">
<title>The Sunny Nook – Business Card</title>
<link href="https://fonts.googleapis.com/css2?family=Bebas+Neue&family=Lilita+One&display=swap" rel="stylesheet">
<style>
  :root {
    --backdrop: #1f1f1f;
    --card: #ffffff;
    --wood: #a85a17;
    --wood-dark: #7a3f0e;
    --sun-orange: #f8a33c;
    --sea-blue: #5cc3dc;
    --sand: #d9a066;
    --brown-text: #a5561a;
    --teal-text: #4cb3d1;
    --crimson-text: #c8103e;
  }
  html, body {
    margin: 0;
    width: 1200px;
    height: 960px;
    overflow: hidden;
    background: var(--backdrop);
  }
  .business-card {
    position: absolute;
    left: 300px;
    top: 309px;
    width: 600px;
    height: 343px;
    background: var(--card);
    border-radius: 18px;
    overflow: hidden;
    font-family: "Bebas Neue", "Arial Narrow", sans-serif;
  }
  .beach-panel {
    position: absolute;
    left: 0;
    top: 0;
  }
  .card-details {
    position: absolute;
    right: 27px;
    top: 0;
    width: 300px;
    height: 343px;
    text-align: right;
  }
  .brand-mark {
    position: absolute;
    right: 8px;
    top: 20px;
    width: 118px;
    text-align: center;
  }
  .brand-dot {
    display: block;
    width: 96px;
    height: 96px;
    margin: 0 auto 6px;
    border-radius: 50%;
    background: var(--sun-orange);
  }
  .brand-name {
    font-size: 24px;
    line-height: 1;
    color: var(--teal-text);
    white-space: nowrap;
  }
  .address {
    position: absolute;
    right: 0;
    top: 170px;
    margin: 0;
    font-style: normal;
    font-size: 20px;
    line-height: 20px;
    color: var(--brown-text);
    white-space: nowrap;
  }
  .phone {
    display: block;
    font-size: 24px;
    line-height: 26px;
    color: var(--teal-text);
  }
  .service-info {
    position: absolute;
    right: 0;
    top: 240px;
    margin: 0;
    white-space: nowrap;
  }
  .cafe-type {
    font-size: 20px;
    line-height: 20px;
    color: var(--brown-text);
  }
  .hours {
    font-size: 15.5px;
    line-height: 16px;
    color: var(--teal-text);
  }
  .cuisine {
    font-size: 12.5px;
    line-height: 12px;
    color: var(--crimson-text);
  }
  .tagline {
    position: absolute;
    right: 0;
    top: 299px;
    font-family: "Lilita One", "Bebas Neue", sans-serif;
    font-weight: 400;
    text-transform: uppercase;
    font-size: 24px;
    line-height: 26px;
    letter-spacing: 1px;
    color: var(--brown-text);
    white-space: nowrap;
  }
</style>
</head>
<body>
  <main class="business-card">
    <svg class="beach-panel" width="340" height="343" viewBox="0 0 340 343">
      <defs>
        <linearGradient id="beach-scene" x1="0" y1="0" x2="0" y2="1">
          <stop offset="0" stop-color="#f8a33c"/>
          <stop offset="0.42" stop-color="#fbb23e"/>
          <stop offset="0.46" stop-color="#5cc3dc"/>
          <stop offset="0.78" stop-color="#8fd6e6"/>
          <stop offset="0.82" stop-color="#d9a066"/>
          <stop offset="1" stop-color="#c98c52"/>
        </linearGradient>
      </defs>
      <circle class="wood-ring" cx="140" cy="172" r="188" fill="var(--wood)"/>
      <circle class="white-ring" cx="140" cy="172" r="155" fill="#ffffff"/>
      <circle class="scene-window" cx="140" cy="172" r="145" fill="url(#beach-scene)"
              role="img" aria-label="Illustration of a smiling tiki character holding a coffee mug and a frying pan with an egg on a sandy beach, with palm leaves, a sunset, seagulls, waves and an ocean liner"/>
    </svg>

    <section class="card-details">
      <div class="brand-mark">
        <span class="brand-dot"></span>
        <span class="brand-name">The Sunny Nook</span>
      </div>

      <address class="address">
        4815C Marlow Grove Avenue<br>
        Long Beach, California
        <span class="phone">P.(555) 731-2294</span>
      </address>

      <p class="service-info">
        <span class="cafe-type">Breakfast &amp; Lunch Cafe</span><br>
        <span class="hours">Open 7 days a week from 7am to 2pm.</span><br>
        <span class="cuisine">Serving traditional American food</span>
      </p>

      <div class="tagline">Locals Only</div>
    </section>
  </main>
</body>
</html>
```